Blue Heron Journeys

We are a predominantly online travel agency with high-end (first/business class) clients. I'm looking to either have our existing logo revamped or a new logo created with business card layout. I prefer to work with existing logo if possible so it remains familiar with existing clientele. I have uploaded a yellow business card layout showing icons on one side of the card. I would like to keep my existing colours, not yellow. could the company name/tag line go over the icons?
Industry/Entity Type
Business
Contact Information for Business Card
Lucinda Fairley
Director
(I.A.T.A. 07715463)
(Corvano Pty. Ltd) ABN 61 574 203 918
512/18 Kendrick Lane
Wattle Reach | NSW 2577 | Australia
www.blueheronjourneys.com.au
m: + 61 (0) 417 588 130
t: + 61 (0) 2 9416 2058
e: lucinda@blueheronjourneys.com.au

```html
<!DOCTYPE html>
<html lang="en">
<head>
<meta charset="utf-8">
<title>Blue Heron Journeys — Business Card</title>
<link href="https://fonts.googleapis.com/css2?family=Lato:wght@400;700&family=Questrial&display=swap" rel="stylesheet">
<style>
  :root {
    --backdrop: #333333;
    --stripe-light: #ffffff;
    --stripe-tint: #e4edf5;
    --ink: #1a1a1a;
    --rule: #8a8a8a;
    --shadow: rgba(0, 0, 0, 0.55);
  }
  * { margin: 0; padding: 0; box-sizing: border-box; }
  html, body { width: 1200px; height: 900px; overflow: hidden; }
  body {
    background: var(--backdrop);
    position: relative;
    font-family: "Lato", sans-serif;
    color: var(--ink);
  }
  .card {
    position: absolute;
    top: 170px;
    width: 347px;
    height: 561px;
    background: repeating-linear-gradient(
      to right,
      var(--stripe-light) 0 12px,
      var(--stripe-tint) 12px 23px
    );
    box-shadow: 3px 4px 6px var(--shadow);
    overflow: hidden;
  }
  .card--front { left: 259px; }
  .card--back { left: 631px; }

  /* front */
  .brand-name {
    position: absolute;
    left: 0; right: 0;
    top: 52px;
    text-align: center;
    font-family: "Lato", sans-serif;
    font-weight: 400;
    font-size: 30px;
    letter-spacing: 0.5px;
    white-space: nowrap;
  }
  .brand-rule {
    position: absolute;
    left: 63px;
    width: 223px;
    top: 102px;
    height: 1px;
    background: var(--rule);
  }
  .tagline {
    font-family: "Questrial", sans-serif;
    font-size: 15px;
    letter-spacing: 1.5px;
    white-space: nowrap;
  }
  .card--front .tagline {
    position: absolute;
    left: 0; right: 0;
    top: 110px;
    text-align: center;
  }
  .contact {
    position: absolute;
    left: 0; right: 0;
    top: 268px;
    text-align: center;
  }
  .contact__name {
    font-weight: 700;
    font-size: 20px;
    line-height: 28px;
  }
  .contact__role {
    font-size: 16px;
    line-height: 22px;
  }
  .contact__rule {
    width: 190px;
    height: 1px;
    margin: 9px auto 11px;
    background: var(--rule);
  }
  .contact__lines {
    font-size: 16px;
    line-height: 21px;
    white-space: nowrap;
  }
  .contact__lines b { font-weight: 700; }
  .contact__company {
    margin-top: 8px;
    font-size: 14px;
    line-height: 19px;
    white-space: nowrap;
  }

  /* back */
  .rotated {
    position: absolute;
    transform: translate(-50%, -50%) rotate(-90deg);
    white-space: nowrap;
  }
  .card--back .brand-name {
    right: auto;
    left: 144px;
    top: 283px;
    font-size: 44px;
    transform: translate(-50%, -50%) rotate(-90deg);
  }
  .card--back .brand-rule {
    left: 196px;
    top: 113px;
    width: 1px;
    height: 334px;
  }
  .card--back .tagline {
    left: 219px;
    top: 280px;
    font-size: 18px;
    letter-spacing: 2px;
  }
</style>
</head>
<body>
  <section class="card card--front" aria-label="Business card front">
    <div class="brand-name">Blue Heron Journeys</div>
    <div class="brand-rule"></div>
    <div class="tagline">travel beyond the ordinary</div>

    <div class="contact">
      <div class="contact__name">LUCINDA FAIRLEY</div>
      <div class="contact__role">Director</div>
      <div class="contact__rule"></div>
      <div class="contact__lines">
        <div><b>m:</b> + 61 (0) 417 588 130</div>
        <div><b>t:</b> + 61 (0) 2 9416 2058</div>
        <div><b>e:</b> lucinda@blueheronjourneys.com.au</div>
        <div><b>w:</b> www.blueheronjourneys.com.au</div>
      </div>
      <div class="contact__rule"></div>
      <div class="contact__lines contact__address">
        <div>512/18 Kendrick Lane</div>
        <div>Wattle Reach | NSW 2577 | Australia</div>
      </div>
      <div class="contact__company">
        <div>(I.A.T.A. 07715463)</div>
        <div>(Corvano Pty. Ltd) ABN 61 574 203 918</div>
      </div>
    </div>
  </section>

  <section class="card card--back" aria-label="Business card back">
    <div class="brand-name">Blue Heron Journeys</div>
    <div class="brand-rule"></div>
    <div class="tagline rotated">travel beyond the ordinary</div>
  </section>
</body>
</html>
```